R7M Horizon Business Card Design

We need a business card created for our New Business "R7M Horizon"<br/><br/>The business card design is up to you however the following information must be on the business card:<br/><br/>Front of the business card -<br/>Email :darrenp@r7mhorizon.nz<br/>Mobile: +64 (0) 22 4870 619<br/>Website: www.r7mhorizon.nz<br/>Card Owner Name: Darren Paltrow<br/>Company Title: Business Development Manager<br/>Slogan: "The BEST of both worlds". <br/>Logo On the front attached to the design brief<br/><br/>On the back: <br/>Space on the back for 4 more versions of the logo across the bottom of the card indicating different subsidiary brands - R7M Coffee, R7M Arts, R7M ?? (The card will be used for all of these brands - We Will add the extra subsidiary logos to the design once the design is finished (We are a graphics design team). <br/><br/>Other than that we want a premium feeling logo that remains universally usable depending on the business entity that we are using the card for. The use of bright bold colours would be great but we still want the card to feel premium.
Target Market(s)
Gift Design and Manufacturing Companies
Contact Information for Business Card
Front of the business card -
Email :darrenp@r7mhorizon.nz
Mobile: +64 (0) 22 4870 619
Website: www.r7mhorizon.nz
Card Owner Name: Darren Paltrow
Company Title: Business Development Manager
Slogan: "The BEST of both worlds".
Logo On the front attached to the design brief

```html
<!DOCTYPE html>
<html lang="en">
<head>
<meta charset="utf-8">
<title>R7M Horizon Business Card</title>
<link rel="stylesheet" href="https://fonts.googleapis.com/css2?family=Montserrat:wght@700;800&family=Arimo:wght@400&display=swap">
<style>
  :root {
    --brand-blue: #3a4aa6;
    --ink: #1e1e24;
    --paper: #ffffff;
    --stage: #e9eaee;
    --rule: #b9b9be;
  }
  * { box-sizing: border-box; margin: 0; padding: 0; }
  html, body { width: 1200px; height: 1015px; overflow: hidden; background: var(--stage); }
  .stage {
    width: 1200px; height: 1015px;
    display: flex; flex-direction: column; align-items: center; justify-content: center; gap: 40px;
  }
  .card { width: 780px; height: 446px; position: relative; overflow: hidden; box-shadow: 0 6px 18px rgba(0,0,0,.18); }

  /* Back */
  .card-back { background: var(--brand-blue); display: flex; align-items: center; justify-content: center; }
  .card-back .pattern-field { position: absolute; inset: 0; background: radial-gradient(circle at 50% 50%, #4050ae 0%, var(--brand-blue) 70%); }
  .card-back .brand-name {
    position: relative; font-family: "Montserrat", sans-serif; font-weight: 800;
    font-size: 40px; color: var(--paper); letter-spacing: 1px;
  }

  /* Front */
  .card-front { background: var(--paper); }
  .front-body { position: absolute; left: 0; top: 0; right: 0; height: 352px; display: flex; align-items: center; }
  .logo-block { width: 380px; display: flex; align-items: center; justify-content: center; padding-top: 60px; }
  .logo-block .brand-name { font-family: "Montserrat", sans-serif; font-weight: 800; font-size: 38px; color: var(--brand-blue); }
  .divider { width: 1px; height: 180px; background: var(--rule); margin-top: 60px; }
  .contact { padding-left: 34px; padding-top: 40px; font-family: "Arimo", sans-serif; color: var(--ink); }
  .contact .person { font-family: "Montserrat", sans-serif; font-weight: 800; font-size: 27px; color: var(--brand-blue); text-transform: uppercase; line-height: 1.05; }
  .contact .role { font-size: 20px; margin-bottom: 10px; }
  .contact ul { list-style: none; }
  .contact li { display: flex; align-items: center; gap: 8px; font-size: 19px; line-height: 1.35; }
  .contact li svg { width: 20px; height: 20px; flex: none; }
  .contact .web-domain { color: var(--brand-blue); }
  .slogan-band {
    position: absolute; left: 0; right: 0; bottom: 0; height: 94px; background: var(--brand-blue);
    display: flex; align-items: center; padding-left: 250px;
  }
  .slogan { font-family: "Montserrat", sans-serif; font-weight: 800; font-size: 22px; letter-spacing: 1.5px; color: var(--paper); }
</style>
</head>
<body>
<main class="stage">
  <section class="card card-back" aria-label="Card back">
    <div class="pattern-field" role="img" aria-label="Faint repeated brand pattern across the blue background"></div>
    <span class="brand-name">R7M Horizon</span>
  </section>

  <section class="card card-front" aria-label="Card front">
    <div class="front-body">
      <div class="logo-block">
        <span class="brand-name">R7M Horizon</span>
      </div>
      <div class="divider" aria-hidden="true"></div>
      <div class="contact">
        <p class="person">Darren Paltrow</p>
        <p class="role">Business Development Manager</p>
        <ul>
          <li>
            <svg viewBox="0 0 20 20" aria-hidden="true"><rect x="1" y="1" width="18" height="18" rx="3" fill="none" stroke="#3a4aa6" stroke-width="2"/><path d="M6 5c-1 1 0 5 3 8s6 3 7 2l-2-3-2 1c-1-.5-3-2.5-3.5-3.5l1-2z" fill="#3a4aa6"/></svg>
            +64 (0) 22 4870 619
          </li>
          <li>
            <svg viewBox="0 0 20 20" aria-hidden="true"><rect x="1" y="4" width="18" height="12" fill="#3a4aa6"/><path d="M1 4l9 7 9-7" fill="none" stroke="#fff" stroke-width="1.5"/></svg>
            darrenp@r7mhorizon.nz
          </li>
          <li>
            <svg viewBox="0 0 20 20" aria-hidden="true"><circle cx="10" cy="10" r="8.5" fill="none" stroke="#3a4aa6" stroke-width="2"/><ellipse cx="10" cy="10" rx="4" ry="8.5" fill="none" stroke="#3a4aa6" stroke-width="1.5"/><path d="M2 10h16M3.5 6h13M3.5 14h13" stroke="#3a4aa6" stroke-width="1.3"/></svg>
            <span>www.<span class="web-domain">r7mhorizon</span>.nz</span>
          </li>
        </ul>
      </div>
    </div>
    <div class="slogan-band">
      <p class="slogan">THE BEST OF BOTH WORLDS</p>
    </div>
  </section>
</main>
</body>
</html>
```